Heritage Hollow Business Cards

Require a business card design. <br/><br/>Needs to include logo (either round or long version) plus these details:<br/>Maya Torvell<br/>Heritage Hollow<br/>maya@kelvadtrading.com.au<br/>02 6481 7395<br/>PO Box Glenwarra NSW 2791<br/>www.heritagehollow.com.au<br/><br/>I need in an editable format so that I can create for multiple staff members. <br/><br/>

Target Market(s)

We are an online store selling renovation products to home owners are builders. Looking for a classic classy design.

Industry/Entity Type

Home And Garden

Contact Information for Business Card

Maya Torvell
Heritage Hollow
maya@kelvadtrading.com.au
02 6481 7395
PO Box Glenwarra NSW 2791
www.heritagehollow.com.au

Colors

Designer to choose colors to be used in the design.

Requirements
Must have
• Must include Logo.

```html
<!DOCTYPE html>
<html lang="en">
<head>
<meta charset="utf-8">
<title>Heritage Hollow Business Cards</title>
<link rel="stylesheet" href="https://fonts.googleapis.com/css2?family=Josefin+Slab:wght@400;600;700&display=swap">
<style>
  :root {
    --backdrop: #8e8e8e;
    --card-light: #fdfcef;
    --card-dark: #2a2a2a;
    --ink: #2b2b2b;
    --ink-soft: #9a998f;
    --chalk: #f2f2ee;
  }
  * { margin: 0; padding: 0; box-sizing: border-box; }
  html, body {
    width: 1200px; height: 960px; overflow: hidden;
    background: var(--backdrop);
    font-family: "Josefin Slab", serif;
  }
  .canvas { position: relative; width: 1200px; height: 960px; }
  .card {
    position: absolute; left: 230px; width: 740px; height: 422px;
  }
  .card--front { top: 38px; background: var(--card-light); color: var(--ink); }
  .card--back { top: 500px; background: var(--card-dark); }

  .wordmark {
    position: absolute; left: 78px; top: 108px;
    font-size: 36px; font-weight: 600; color: var(--ink); letter-spacing: 0.2px;
  }
  .person { position: absolute; left: 75px; top: 232px; }
  .person__name { font-size: 28px; font-weight: 700; letter-spacing: 1px; text-transform: uppercase; }
  .person__role { font-size: 19px; color: var(--ink-soft); margin-top: 2px; }

  .contact { position: absolute; left: 411px; top: 238px; font-size: 17.5px; letter-spacing: 0.4px; }
  .contact__company { color: var(--ink); }
  .contact__address { color: var(--ink-soft); margin-top: 8px; }
  .contact__list { list-style: none; margin-top: 14px; }
  .contact__item { display: flex; align-items: center; gap: 9px; color: var(--ink-soft); height: 26.5px; }
  .contact__icon { width: 14px; height: 14px; flex: none; }

  .emblem {
    position: absolute; left: 250px; top: 88px; width: 266px; height: 266px;
    border: 1.5px solid var(--chalk); border-radius: 50%;
  }
  .emblem__name {
    position: absolute; left: 278px; top: 228px;
    font-size: 38px; font-weight: 600; line-height: 1.0; color: var(--chalk);
  }
</style>
</head>
<body>
<main class="canvas">
  <section class="card card--front">
    <div class="wordmark">Heritage Hollow</div>

    <div class="person">
      <div class="person__name">Maya Torvell</div>
      <div class="person__role">Founder &amp; CEO</div>
    </div>

    <div class="contact">
      <div class="contact__company">Heritage Hollow</div>
      <div class="contact__address">PO Box Glenwarra NSW 2791</div>
      <ul class="contact__list">
        <li class="contact__item">
          <svg class="contact__icon" viewBox="0 0 16 16"><path d="M4 1 L6.5 4.5 L5 6 C6 8.5 7.5 10 10 11 L11.5 9.5 L15 12 L13 15 C7 14 2 9 1 3 Z" fill="#2b2b2b"/></svg>
          02 6481 7395
        </li>
        <li class="contact__item">
          <svg class="contact__icon" viewBox="0 0 16 16"><rect x="1" y="3.5" width="14" height="9" fill="#2b2b2b"/><path d="M1.5 4 L8 9 L14.5 4" stroke="#fdfcef" stroke-width="1.3" fill="none"/></svg>
          maya@kelvadtrading.com.au
        </li>
        <li class="contact__item">
          <svg class="contact__icon" viewBox="0 0 16 16" fill="none" stroke="#2b2b2b" stroke-width="1.3"><circle cx="8" cy="8" r="6.5"/><ellipse cx="8" cy="8" rx="3" ry="6.5"/><path d="M1.5 8 H14.5 M2.5 4.8 H13.5 M2.5 11.2 H13.5"/></svg>
          www.heritagehollow.com.au
        </li>
      </ul>
    </div>
  </section>

  <section class="card card--back">
    <div class="emblem"></div>
    <div class="emblem__name">Heritage<br>Hollow</div>
  </section>
</main>
</body>
</html>
```